I am looking for a modern, clean and neat design for a reflexology and well being business. The business name is Gralo Tund (this is an old Latin word for wellbeing). The colours I would like are purple, white and grey. I am open to suggestions for pictures such as healing or working hands, a pair of feet, images that represent my business that you may think of....... or maybe you think no images at all would be best? My tag line is: "Relax, Renew, Revive" or "Find you balance......... Relax, Renew, Revive" I can decide which I want so I would like to see what both would look like. I would like space on the back to write the client's appointment date and time (more than once)

```html
<!DOCTYPE html>
<html lang="en">
<head>
<meta charset="utf-8">
<title>Gralo Tund – Business Card</title>
<link href="https://fonts.googleapis.com/css2?family=PT+Sans:wght@400;700&display=swap" rel="stylesheet">
<style>
  :root {
    --purple: #652d8c;
    --grey: #9a9a9a;
    --grey-light: #c9c9c9;
    --ink-grey: #7a7a7a;
    --white: #ffffff;
    --backdrop: #efebe4;
    --photo-top: #f4f1f0;
    --photo-mid: #e6dfe0;
    --photo-low: #d9dcdf;
  }
  html, body {
    margin: 0;
    width: 1189px;
    height: 1200px;
    overflow: hidden;
    background: var(--backdrop);
    font-family: "PT Sans", sans-serif;
  }
  .card {
    position: absolute;
    left: 182px;
    width: 832px;
    height: 488px;
    border-radius: 34px;
    background: var(--white);
    overflow: hidden;
    box-shadow: 0 8px 18px rgba(0,0,0,0.18);
  }
  .card--front { top: 67px; }
  .card--back { top: 626px; }
  .card svg { display: block; width: 100%; height: 100%; }
  .brand-name { font-family: "PT Sans", sans-serif; font-weight: 700; font-size: 92px; fill: var(--purple); }
  .tagline { font-family: "PT Sans", sans-serif; font-size: 20px; letter-spacing: 2.4px; fill: var(--ink-grey); }
  .employee { font-family: "PT Sans", sans-serif; font-weight: 700; font-size: 35px; fill: var(--white); }
  .contact { font-family: "PT Sans", sans-serif; font-size: 27px; fill: var(--white); }
  .appt-title { font-family: "PT Sans", sans-serif; font-size: 38px; fill: var(--purple); }
  .day-label { font-family: "PT Sans", sans-serif; font-size: 24px; fill: var(--purple); }
  .field-label { font-family: "PT Sans", sans-serif; font-size: 28px; fill: var(--purple); }
  .website { font-family: "PT Sans", sans-serif; font-weight: 700; font-size: 28px; fill: var(--purple); }
  .rule { stroke: var(--grey); stroke-width: 1.5; }
  .tick-box { fill: none; stroke: var(--grey); stroke-width: 1.5; }
</style>
</head>
<body>

<section class="card card--front">
  <svg viewBox="0 0 1020 598" xmlns="http://www.w3.org/2000/svg">
    <defs>
      <linearGradient id="spa-photo-tone" x1="0" y1="0" x2="1" y2="1">
        <stop offset="0" stop-color="#f2c6cc"/>
        <stop offset="0.35" stop-color="var(--photo-top)"/>
        <stop offset="0.7" stop-color="var(--photo-mid)"/>
        <stop offset="1" stop-color="var(--photo-low)"/>
      </linearGradient>
    </defs>
    <rect class="spa-photo" x="0" y="60" width="600" height="480" fill="url(#spa-photo-tone)"
          role="img" aria-label="Photo of stacked black spa stones on a rolled white towel with pink flowers and pebbles"/>
    <path class="wave-grey" d="M0 405 C 60 470 160 505 300 500 C 500 490 640 390 800 360 C 860 350 900 352 960 356 L 1020 380 L 1020 598 L 0 598 Z" fill="var(--grey)"/>
    <path class="wave-white" d="M0 455 C 80 515 200 540 340 528 C 520 510 640 410 800 375 C 880 358 950 362 1020 400 L 1020 598 L 0 598 Z" fill="var(--white)"/>
    <path class="wave-purple" d="M0 478 C 90 525 220 548 360 536 C 540 520 660 425 830 372 C 900 356 970 375 1020 400 L 1020 598 L 0 598 Z" fill="var(--purple)"/>

    <text class="brand-name" x="976" y="208" text-anchor="end">Gralo Tund</text>
    <text class="tagline" x="976" y="236" text-anchor="end">Find you balance......... Relax, Renew, Revive</text>

    <text class="employee" x="976" y="459" text-anchor="end">Employee Name</text>
    <text class="contact" x="938" y="515" text-anchor="end">123-456-7890</text>
    <text class="contact" x="938" y="548" text-anchor="end">yourname@gralotund.com</text>

    <g class="icon-phone" transform="translate(948 493)">
      <rect width="27" height="25" rx="4" fill="var(--white)"/>
      <path d="M6 10 Q13.5 4 21 10 L19 12 L16 11 L16 9 Q13.5 8 11 9 L11 11 L8 12 Z" fill="var(--purple)"/>
      <rect x="8" y="13" width="11" height="7" rx="1.5" fill="var(--purple)"/>
    </g>
    <g class="icon-mail" transform="translate(948 526)">
      <rect width="27" height="25" rx="4" fill="var(--white)"/>
      <rect x="5" y="6" width="17" height="13" fill="none" stroke="var(--purple)" stroke-width="2"/>
      <path d="M5 6 L13.5 13 L22 6 M5 19 L11 12.5 M22 19 L16 12.5" fill="none" stroke="var(--purple)" stroke-width="1.6"/>
    </g>
  </svg>
</section>

<section class="card card--back">
  <svg viewBox="0 0 1020 598" xmlns="http://www.w3.org/2000/svg">
    <line class="rule" x1="94" y1="181" x2="928" y2="181"/>
    <text class="appt-title" x="507" y="240" text-anchor="middle">Has An Appoinment On</text>

    <g class="day-options">
      <rect class="tick-box" x="92" y="295" width="33" height="33"/>
      <text class="day-label" x="148" y="327">Mon</text>
      <rect class="tick-box" x="238" y="295" width="33" height="33"/>
      <text class="day-label" x="292" y="327">Tues</text>
      <rect class="tick-box" x="384" y="295" width="33" height="33"/>
      <text class="day-label" x="442" y="327">Wed</text>
      <rect class="tick-box" x="530" y="295" width="33" height="33"/>
      <text class="day-label" x="583" y="327">Thur</text>
      <rect class="tick-box" x="676" y="295" width="33" height="33"/>
      <text class="day-label" x="729" y="327">Fri</text>
      <rect class="tick-box" x="820" y="295" width="33" height="33"/>
      <text class="day-label" x="874" y="327">Sat</text>
    </g>

    <text class="field-label" x="93" y="396">Date</text>
    <line class="rule" x1="203" y1="395" x2="542" y2="395"/>
    <text class="field-label" x="565" y="396">AT</text>
    <line class="rule" x1="616" y1="395" x2="862" y2="395"/>
    <text class="field-label" x="882" y="388">am.</text>
    <text class="field-label" x="882" y="412">pm.</text>

    <text class="website" x="511" y="540" text-anchor="middle">www.gralotund.com</text>
  </svg>
</section>

</body>
</html>
```